Law Firm in Texas in need of new letterhead

Law Firm in Fort Worth, TX, USA named "Pell & Varnum, Attorneys-At-Law, LLP." This is a general practice law firm that mostly does Family Law and Criminal Defense work.

We are looking for a new letterhead that has a "classical" appeal, with modern elements.

Any color combination is fine, but please note that we do fax many documents, so the design must be clearly legible in Black and White.

We would like our letterhead to project a sense of professionalism, integrity, and ability.

Target Market(s)

Letterhead will be for correspondence generally with other attorneys and clients.

Industry/Entity Type

Law Firm

Logo Text

Pell & Varnum, Attorneys-At-Law, LLP.

Logo styles of interest
Pictorial/Combination Logo
Wordmark Logo
Lettermark Logo
Requirements
Nice to have
• Although not necessary, a "Texas Star" that is incorporated into the design would be a nice touch.
Should not have
• Colors that do not convert to B&W easily

```html
<!DOCTYPE html>
<html lang="en">
<head>
<meta charset="utf-8">
<title>Pell &amp; Varnum Letterhead</title>
<link href="https://fonts.googleapis.com/css2?family=Carlito:wght@400;700&display=swap" rel="stylesheet">
<style>
  :root {
    --backdrop: #e9e6e2;
    --paper: #ffffff;
    --ink: #231f20;
    --band: #231f20;
    --band-text: #ffffff;
    --watermark: #ededee;
    --rule: #231f20;
  }
  * { margin: 0; padding: 0; box-sizing: border-box; }
  html, body { width: 1200px; height: 1000px; overflow: hidden; }
  body {
    background: var(--backdrop);
    font-family: "Carlito", "Calibri", sans-serif;
    color: var(--ink);
    position: relative;
  }
  .sheet {
    position: absolute;
    top: 110px;
    width: 557px;
    height: 788px;
    background: var(--paper);
    box-shadow: 0 2px 6px rgba(0,0,0,0.25);
    overflow: hidden;
  }
  .sheet--letter { left: 43px; }
  .sheet--blank { left: 613px; }

  .header { position: absolute; top: 10px; left: 0; width: 100%; height: 42px; }
  .header__accent { position: absolute; left: 0; top: 0; width: 10px; height: 42px; background: var(--band); }
  .header__firm {
    position: absolute; left: 19px; top: 11px;
    font-size: 17px; font-weight: 700; letter-spacing: 0.1px; white-space: nowrap;
  }
  .header__contact {
    position: absolute; right: 0; top: 0; width: 250px; height: 42px;
    background: var(--band); color: var(--band-text);
    font-size: 11.5px; line-height: 14px;
  }
  .contact__address { position: absolute; left: 14px; top: 7px; }
  .contact__lines { position: absolute; left: 149px; top: 7px; }
  .contact__line { display: flex; align-items: center; gap: 4px; }
  .contact__line svg { width: 9px; height: 9px; fill: var(--band-text); }

  .watermark {
    position: absolute; left: 94px; top: 210px;
    width: 370px; height: 370px; border-radius: 50%;
    background: var(--watermark);
  }

  .letter {
    position: absolute; left: 39px; top: 145px;
    font-size: 10.6px; line-height: 13.5px; white-space: nowrap;
  }
  .letter p { margin-bottom: 13.5px; }
  .letter .salutation { margin-bottom: 12px; }
  .letter .signature { padding-left: 3px; }

  .footer {
    position: absolute; left: 0; right: 0; top: 741px;
    border-top: 2px solid var(--rule);
    padding: 5px 2px 0;
    font-size: 8.6px; line-height: 11px; white-space: nowrap;
  }
  .footer strong { font-weight: 700; }
</style>
</head>
<body>

<svg width="0" height="0" style="position:absolute">
  <symbol id="icon-phone" viewBox="0 0 10 10"><path d="M2.2 0.5 3.6 2.6 2.7 3.6C3.3 5 4.8 6.6 6.4 7.3L7.4 6.4 9.5 7.8 8.6 9.5C4.5 9.3 0.7 5.5 0.5 1.4Z"/></symbol>
  <symbol id="icon-fax" viewBox="0 0 10 10"><path d="M2.5 0.5H7.5V3H2.5Z M0.5 3.5H9.5V7.5H8V6H2V7.5H0.5Z M2.5 6.5H7.5V9.5H2.5Z"/></symbol>
</svg>

<article class="sheet sheet--letter">
  <header class="header">
    <div class="header__accent"></div>
    <div class="header__firm">Pell &amp; Varnum, Attorneys-At-Law, LLP.</div>
    <div class="header__contact">
      <div class="contact__address">2718 W. Rosedale St.<br>Fort Worth, TX 76104</div>
      <div class="contact__lines">
        <div class="contact__line"><svg><use href="#icon-phone"/></svg>(817) 555-0142</div>
        <div class="contact__line"><svg><use href="#icon-fax"/></svg>(817) 555-0187</div>
      </div>
    </div>
  </header>

  <div class="watermark" role="img" aria-label="Faint Texas star in a circle watermark"></div>

  <section class="letter">
    <p class="salutation">Dear Addressee Name:</p>
    <p>Andipsum dipsum nostis nulpute magnissis niatie te molor adignis sequips uscipisit, sit vel ipsuscing ent<br>
    lut lan ulla feugait augueraesto odolore doluptatio cons dolor sismodo luptatuero do od dolore magnim<br>
    dolor auguero eu facilis ea core estrud eugiat velis ad tat dio odolor augue magna corting eugait enim<br>
    venibh et, quatumsan hendre tincinisi tisisl dolute moloreet atem velesequat alit aliquat, vel dolore<br>
    faciduis dolore dignis dolorper il eugiamconsed deliquamcon henis alis atum duis at.<br>
    Bore del ute faccum vercill aorper sent alit, venis autet, quipsustio eugue vero dolore velendre euis nos<br>
    nonse dolessim illa feum dolor sumsan ectet lortincin vulputat amet, qui esto conulput acil in eugait vel<br>
    essequam zzriusto diam, velit wissit autat.<br>
    Obore dolor incip ea conummy nulput vel ullan henisim am in ute erciliqui ex ent et, quis augiat,<br>
    commod tis enis num delit laor acing elis dolorer se eugue feu facinci liquis aut lut nulluptat er sum zzrit<br>
    vulla consequis accum incidunt iusci blaortio odoloreet pratum veliquatie modit, quat. Ut nummodo<br>
    exercilisl iriliqu ipsusto dolesequat. Ut wisl in ute consequam ad diam vulputpat lan hent vel doloreet<br>
    utat ver si.</p>
    <p>Vullaorem iusci blamcon seniamcommy nit iureetum dolore con ea faccum iureet prat. In utat acidunt<br>
    nullum venismolum ing exer iusci bla augue magna consequi tem veliquis nostion utpat.<br>
    Nibh euipis esed ero doluptat. Ibh ex exeros exero dolesed dunt pratissi euis nismodipsum eu feuguerit<br>
    ipisl incilla faccum am init praese tat velis augue corem iriliqu amconsequat. Magnim ipit in ea acincil<br>
    esto et wisl esenim volenit lorem del ut aut la commy nibh eui tiniam iure mod tem vel ipisit, quis nonse-<br>
    qui blan exerosto odolorem il irit num vel dolore et irit aute te dolestrud tin hent utet ut praestrud ea<br>
    faccum venim venim il er iustion sequipsum quat.</p>
    <p>Do ea acilisis dolore min ercing endre consequat. Ero consequis ad euguerat, siscidunt laor sum iuscipis<br>
    nullaoreet, velent ilit amconul laorperit lore diatum dui bla facipit irit alis ad dolorpe rostrud tem esse-<br>
    quat praesequam, coreet ip er sim dit, velisim inciliquam, quis adigna feugue dolore et irillaor.<br>
    Adiam zzrit,</p>
    <p class="signature">Veliquatin Veraessi</p>
  </section>

  <footer class="footer">
    Partners:<br>
    <strong>Martin Pell</strong>, Managing Partner (Licensed in State of Texas, United States District Court (Northern District of Texas), United States Supreme Court)<br>
    <strong>Diane Louise Varnum</strong> (Licensed in the State of Texas)
  </footer>
</article>

<article class="sheet sheet--blank">
  <header class="header">
    <div class="header__accent"></div>
    <div class="header__firm">Pell &amp; Varnum, Attorneys-At-Law, LLP.</div>
    <div class="header__contact">
      <div class="contact__address">2718 W. Rosedale St.<br>Fort Worth, TX 76104</div>
      <div class="contact__lines">
        <div class="contact__line"><svg><use href="#icon-phone"/></svg>(817) 555-0142</div>
        <div class="contact__line"><svg><use href="#icon-fax"/></svg>(817) 555-0187</div>
      </div>
    </div>
  </header>

  <div class="watermark" role="img" aria-label="Faint Texas star in a circle watermark"></div>

  <footer class="footer">
    Partners:<br>
    <strong>Martin Pell</strong>, Managing Partner (Licensed in State of Texas, United States District Court (Northern District of Texas), United States Supreme Court)<br>
    <strong>Diane Louise Varnum</strong> (Licensed in the State of Texas)
  </footer>
</article>

</body>
</html>
```